Elegant Business Card for Technology Company

Client is a supplier of innovative industrial communications and automation equipment since 2002. This contest is to gather fresh ideas for a redesign of the existing business card. Client is looking for design that best communicates tagline "Industrial Networking and Computing Specialist".

Design submissions should look modern, clean, elegant and professional. It should not be cluttered. Use white as the primary colour. Orange and black as secondary colour. Refer to jpeg File 1 on the current design.

Fonts used by Client used include Arial Regular, Arial Black, Roboto Regular, Roboto Black and Lato.

The winning design will be sent for offset printing using super white 250gsm artcard paper (open for suggestions).

Target Market(s)

System Engineers, Project Managers, Purchasing Managers from companies providing engineering services for Smart Cities.

Industry/Entity Type

Information Technology

Contact Information for Business Card

Refer to PDF File 3 for Business Card Details. Priority of short contact information would be as follows Name > Job Title > Email > Mobile > Web > Tel > Fax > Business Address >UEN (UEN represents company registration number)

Font styles to use
Sans Serif

Colors
ffffff
f37122
000000
5c5c5c

Requirements
Must have
• Refer to AI File 2 (Company Logo) & PDF File 3 (Information on Namecard)
Should not have
• No QR codes
• No Social Media Icons
• Do not create full Black or Orange colour background

```html
<!DOCTYPE html>
<html lang="en">
<head>
<meta charset="utf-8">
<title>Korvane Business Card</title>
<link href="https://fonts.googleapis.com/css2?family=Lato:wght@400;700;900&display=swap" rel="stylesheet">
<style>
  :root {
    --white: #ffffff;
    --orange: #f37122;
    --black: #000000;
    --ink: #1a1a1a;
    --grey: #5c5c5c;
    --stage: #2b2b2b;
  }
  * { margin: 0; padding: 0; box-sizing: border-box; }
  html, body { width: 1200px; height: 1166px; overflow: hidden; }
  body {
    background: var(--stage);
    font-family: "Lato", Arial, sans-serif;
    color: var(--ink);
    position: relative;
  }
  .card {
    position: absolute;
    left: 220px;
    width: 760px;
    height: 434px;
    background: var(--white);
    overflow: hidden;
  }
  .card-front { top: 90px; }
  .card-back { top: 630px; top: 640px; }

  .brand {
    display: flex;
    align-items: center;
    gap: 14px;
  }
  .brand-dot {
    width: 58px; height: 58px;
    border-radius: 50%;
    background: var(--orange);
  }
  .brand-name {
    font-weight: 900;
    font-size: 58px;
    letter-spacing: 2px;
    color: var(--black);
    line-height: 1;
  }

  /* front */
  .card-front .brand { position: absolute; left: 200px; top: 120px; }
  .tagline {
    position: absolute; left: 0; right: 0; top: 222px;
    text-align: center;
    font-weight: 900;
    font-size: 19px;
    color: var(--ink);
  }
  .services {
    position: absolute; left: 0; right: 0; top: 268px;
    text-align: center;
    font-size: 17px;
    line-height: 1.45;
    color: var(--ink);
  }
  .bullet { color: var(--orange); padding: 0 4px; }

  /* back */
  .card-back .brand { position: absolute; right: 60px; top: 40px; }
  .person { position: absolute; right: 70px; top: 140px; text-align: right; }
  .person-name { font-size: 27px; color: var(--ink); }
  .person-role { font-size: 21px; color: var(--orange); }

  .company { position: absolute; left: 60px; top: 150px; font-size: 19px; line-height: 1.25; }
  .company-name { color: var(--orange); }
  .contacts { list-style: none; margin-top: 10px; }
  .contacts li { display: flex; align-items: center; gap: 12px; }
  .contacts svg { width: 16px; height: 16px; fill: var(--orange); flex: none; }
  .uen { margin-top: 10px; }

  .swoosh { position: absolute; left: 0; top: 0; width: 760px; height: 434px; }
  .website {
    position: absolute; right: 40px; bottom: 22px;
    color: var(--white);
    font-size: 18px;
    letter-spacing: 1px;
  }
</style>
</head>
<body>

  <section class="card card-front">
    <div class="brand">
      <span class="brand-dot"></span>
      <span class="brand-name">KORVANE</span>
    </div>
    <p class="tagline">Industrial Networking and Computing Specialist</p>
    <p class="services">
      Industrial Ethernet / Wireless / Cellular<span class="bullet">•</span>Industrial and Embedded Computing<br>
      Serial / Fieldbus Connectivity<span class="bullet">•</span>IP Video Surveillance<span class="bullet">•</span>Remote Automation
    </p>
  </section>

  <section class="card card-back">
    <svg class="swoosh" viewBox="0 0 760 434" aria-hidden="true">
      <path d="M0 434 Q420 400 760 228 L760 434 Z" fill="var(--orange)"/>
      <path d="M0 434 Q430 404 760 246 L760 434 Z" fill="var(--white)"/>
      <path d="M0 434 Q440 408 760 254 L760 434 Z" fill="var(--ink)"/>
    </svg>

    <div class="brand">
      <span class="brand-dot"></span>
      <span class="brand-name">KORVANE</span>
    </div>

    <div class="person">
      <p class="person-name">Daniel Lim</p>
      <p class="person-role">Sales manager</p>
    </div>

    <div class="company">
      <p class="company-name">Korvane Asia Pacific Pte Ltd</p>
      <p>22 Harbour Lane<br>Meridian Park #05-12 (Block B)<br>Singapore 400123</p>
      <ul class="contacts">
        <li><svg viewBox="0 0 16 16"><path d="M3 1l3 3-2 2c1 2 3 4 5 5l2-2 3 3-2 3C6 15 1 10 1 3z"/></svg>+65 6100 2040</li>
        <li><svg viewBox="0 0 16 16"><path d="M4 0h8v16H4zM5.5 2v10h5V2z"/></svg>+65 9100 3000</li>
        <li><svg viewBox="0 0 16 16"><path d="M4 1h8v4H4zM1 6h14v6h-3v3H4v-3H1zM5 10v4h6v-4z"/></svg>+65 6100 2041</li>
        <li><svg viewBox="0 0 16 16"><path d="M1 3h14v10H1zM2 4l6 5 6-5z" fill-rule="evenodd"/></svg>sales@korvane.com.sg</li>
      </ul>
      <p class="uen">UEN No 200200000K</p>
    </div>

    <p class="website">www.korvane.com.sg</p>
  </section>

</body>
</html>
```